Cash Balance Retirement Plan Services Page

We are looking to have a services/landing page created for one of our offerings. The goal of the page is to explain a relatively complex service (advanced retirement plan) by highlighting the benefits and uses for the plan such that it tells a story that encourages individuals and businesses that would benefit from the plans to reach out.

The page will be used both as a landing page (though secondarily) and as a page that many of our partners will show to their clients in order to generate interest. We help other people closes these deals so we want it to handle both.

Overall, we would want the page to incorporate the following sections/areas.
1. Headline and a place for a video at the top
2. Explanation of what a cash balance plan is (a paragraph or two)
3. These five benefits: These are the 7 we usually use, but only include five at a time so only need room for five.
a. Highest Tax Deductible Contributions Allowed
b. Significantly reduce your taxes
c. Potential Negative “Net Cost”
d. Owner & Executive Weighted Benefits
e. Retain and Attract Top Talen
f. Catch Up On decades of low retirement savings in a matter of years
g. Potential for life time income
4. A section comparing the contribution limits allowed for each plan type (Please see attached image as an example).
5. A place for a table of contribution amounts (This will just be an image. Also, attached).
6. A place for a compare table
6. Who should consider such a plan
7. Occasional banners for call to actions
8. FAQ

Our primary audience for this project are successful small business owners with a particular focus on medical professionals (doctors, chiropractors, dentists, plastic surgeons, etc.). In generally, they will be between 45 and 65 years old and earn $150k or more.

Because we work a lot with financial, business strategy, and insurance based products that require a significant investment by the client trust, professionalism, and sophistication are important attributes we wish to portray in the design of the page. Our preferred colors are blue or green. Though we are still working on figuring out the color scheme so your input as a designer is welcomed as your creativity can help us communicate the attributes we seek to embody for our clients.

In the attached document, I have included some additional information about the service itself if it helps to have some context, as well as a more flushed out outline of the details above.

Importantly, I am not a marketer so any creative input is always welcome if there is a best practice we are not incorporating in either our design requests or outline.

Here is the URL for our current page: https://www.brightvaleadvisors.com/physicianplan

Please don't let this page be your muse. We're trying to get away from it for a reason :) But it still will hopefully provide some helpful information, copy examples, and context.

Additionally, please don't feel like you need to read the full cash balance explanation. That's only if context will be helpful.

We are also going through a rebranding so please don't rely on the colors from the BrightValeAdvisors logo you may see on the website. I've attached two sample logos for the rebrand for context.

```html
<!DOCTYPE html>
<html lang="en">
<head>
<meta charset="utf-8">
<title>Highcrest Financial — Cash Balance Plan</title>
<link href="https://fonts.googleapis.com/css2?family=Montserrat:wght@400;500;600;700;800&family=Roboto:wght@400;500;700&display=swap" rel="stylesheet">
<style>
:root{
  --navy:#0b4a8f;
  --navy-deep:#0a3f86;
  --royal:#0d1990;
  --ink:#2b2f36;
  --muted:#4a4f57;
  --grey-bg:#f1f2f5;
  --line:#d9dde5;
  --white:#ffffff;
  --footer:#1c1c1e;
  --row-a:#c8d2ef;
  --row-b:#e6eaf6;
  --bar-ira:#7dc242;
  --bar-401k:#1fa84a;
  --bar-ps:#86b9ee;
  --bar-cb:#1560d2;
}
*{box-sizing:border-box;margin:0;padding:0}
html,body{width:1200px;height:4389px;overflow:hidden}
body{font-family:"Montserrat",sans-serif;color:var(--ink);background:var(--white);position:relative}
.abs{position:absolute}
/* header */
.site-header{position:absolute;top:0;left:0;width:1200px;height:68px;background:var(--white);z-index:5}
.brand{position:absolute;display:flex;align-items:center;gap:8px;color:var(--navy);font-weight:800;text-transform:uppercase;line-height:.95}
.brand-dot{border-radius:50%;background:var(--navy);flex:none}
.site-header .brand{left:132px;top:14px;font-size:17px}
.site-header .brand-dot{width:44px;height:44px}
.main-nav{position:absolute;left:394px;top:22px;display:flex;gap:0;font-size:12.5px;font-weight:600;color:var(--ink)}
.main-nav a{color:inherit;text-decoration:none;padding:3px 6px;margin-right:18px}
.main-nav a.active{border:1.5px solid var(--navy);color:var(--navy)}
.call{position:absolute;left:914px;top:18px;display:flex;gap:10px;align-items:center}
.call-icon{width:28px;height:28px;border-radius:50%;background:var(--navy);display:flex;align-items:center;justify-content:center}
.call small{display:block;font-size:9px;font-weight:600;color:var(--muted)}
.call strong{display:block;font-size:14px;color:var(--navy);font-weight:700}
/* hero */
.hero{position:absolute;top:68px;left:0;width:1200px;height:600px;background:linear-gradient(90deg,#2d3644 0%,#5b6674 45%,#9aa6b3 70%,#c6cdd6 100%)}
.hero-welcome{position:absolute;left:141px;top:120px;border:2px solid #fff;color:#fff;font-size:20px;font-weight:600;padding:6px 12px;letter-spacing:.5px}
.hero h1{position:absolute;left:139px;top:176px;color:#fff;font-size:43px;font-weight:800;line-height:1.15;text-transform:uppercase}
.btn-outline{position:absolute;left:143px;top:307px;width:167px;height:46px;border:2px solid #fff;background:var(--navy-deep);color:#fff;font-size:14px;font-weight:600;display:flex;align-items:center;justify-content:center}
.play{position:absolute;left:556px;top:258px}
.hero-wave{position:absolute;left:0;top:600px}
/* about */
.about{position:absolute;top:656px;left:0;width:1200px;height:448px}
.about-photo{position:absolute;left:0;top:0;width:700px;height:448px;background:linear-gradient(90deg,#c9cdd3 0%,#e6e8ec 55%,#ffffff 100%)}
.section-title{font-weight:700;color:var(--navy);text-transform:uppercase;font-size:19px}
.about h2{position:absolute;left:714px;top:98px;font-size:18.5px;color:#1d2330}
.about h2 span{color:var(--navy)}
.about p{position:absolute;left:716px;top:172px;width:370px;font-size:13.6px;line-height:22.5px;color:var(--muted)}
/* benefits */
.benefits{position:absolute;top:1104px;left:0;width:1200px;height:720px;background:var(--grey-bg)}
.center-title{position:absolute;left:0;width:1200px;text-align:center}
.rule{display:block;width:30px;height:3px;background:var(--navy);margin:14px auto 0}
.card{position:absolute;background:#fff;box-shadow:0 2px 8px rgba(0,0,0,.07)}
.card-tall{top:110px;width:299px;height:329px;text-align:center;padding:22px 20px}
.card-tall h3{font-size:13.5px;font-weight:500;color:#1d2330;line-height:19px;margin-top:14px}
.card-tall p{font-size:10.8px;line-height:17px;color:var(--muted);margin-top:12px}
.card-wide{top:456px;width:459px;height:146px;display:flex;padding:30px 30px 0 36px;gap:30px}
.card-wide h3{font-size:13.5px;font-weight:500;color:#1d2330}
.card-wide p{font-size:10.8px;line-height:17px;color:var(--muted);margin-top:12px;width:240px}
.benefits-wave{position:absolute;left:0;top:640px}
/* table */
.contrib{position:absolute;top:1824px;left:0;width:1200px;height:511px;background:#fff}
.contrib .center-title{top:66px;font-size:18px}
.rates{position:absolute;left:198px;top:146px;border-collapse:collapse;font-family:"Roboto",sans-serif;box-shadow:0 0 0 3px #e2e5ec,0 3px 8px rgba(0,0,0,.2);background:#fff}
.rates th{background:var(--royal);color:#fff;text-align:left;vertical-align:top;font-size:19px;font-weight:500;line-height:26px;padding:6px 10px;height:119px;border-right:2px solid #fff}
.rates td{font-size:20px;padding:0 10px;height:36px;border-right:2px solid #fff;border-top:2px solid #fff;color:#111}
.rates tr:nth-child(odd) td{background:var(--row-a)}
.rates tr:nth-child(even) td{background:var(--row-b)}
.rates td.key{font-weight:700}
/* chart */
.compare{position:absolute;top:2335px;left:0;width:1200px;height:580px;background:linear-gradient(135deg,#f3f4f6,#e9eaee)}
.compare .center-title{top:56px;font-size:18px}
.chart-label{position:absolute;font-family:Arial,sans-serif;font-weight:700;font-size:17px;color:#111;text-align:center;line-height:20px}
.bar{position:absolute}
.chart-note{position:absolute;left:880px;top:190px;width:115px;font-family:Arial,sans-serif;font-size:15px;line-height:19px;text-align:center;color:#111}
.compare-wave{position:absolute;left:0;top:520px}
/* who */
.who{position:absolute;top:2915px;left:0;width:1200px;height:690px;background:#fff}
.who h2{position:absolute;left:133px;top:62px;font-size:18.5px}
.who .intro{position:absolute;left:133px;top:121px;width:390px;font-size:13.6px;line-height:22.5px;color:var(--muted)}
.criteria{position:absolute;left:133px;top:237px;width:436px;height:310px;background:var(--grey-bg);padding:28px 24px 0 24px;list-style:none}
.criteria li{position:relative;padding-left:22px;font-size:11.8px;line-height:17.5px;color:var(--muted);margin-bottom:20px}
.criteria li::before{content:"";position:absolute;left:0;top:5px;width:8px;height:8px;border-radius:50%;background:var(--navy)}
.cta{position:absolute;left:133px;top:576px;width:437px;height:52px;background:var(--navy);color:#fff;font-size:14px;font-weight:600;display:flex;align-items:center;justify-content:center;gap:16px;text-transform:uppercase}
.who-photo{position:absolute;left:605px;top:65px;width:464px;height:563px;background:linear-gradient(180deg,#e8ebef 0%,#d6dbe2 60%,#c3cad3 100%)}
/* faq */
.faq{position:absolute;top:3605px;left:0;width:1200px;height:560px;background:linear-gradient(180deg,#0c4a94,#0a3f88)}
.faq .center-title{top:40px;color:#fff;font-size:18px}
.faq .rule{background:#fff}
.faq-list{position:absolute;left:341px;top:112px;width:520px;list-style:none}
.faq-list li{height:68px;border-bottom:1.5px solid rgba(255,255,255,.85);color:#fff;font-size:15.5px;display:flex;justify-content:space-between;align-items:flex-start;padding-top:10px;margin-bottom:0}
.faq-list li + li{margin-top:0}
.chev{width:24px;height:24px;border:1.5px solid #fff;border-radius:50%;display:flex;align-items:center;justify-content:center;margin-top:4px}
/* footer */
.site-footer{position:absolute;top:4100px;left:0;width:1200px;height:289px}
.footer-wave{position:absolute;left:0;top:0}
.site-footer .brand{left:132px;top:110px;font-size:27px;color:#7e8aa0}
.site-footer .brand-dot{width:64px;height:64px;background:var(--navy)}
.follow{position:absolute;left:838px;top:98px;display:flex;align-items:center;gap:12px;color:#fff;font-size:12px;font-weight:500}
.social{width:34px;height:34px;border-radius:50%;background:var(--navy)}
.footer-nav{position:absolute;left:577px;top:156px;display:flex;gap:30px;font-size:13px;color:#fff;font-weight:500}
.copyright{position:absolute;left:0;top:246px;width:1200px;text-align:center;color:#fff;font-size:11.5px}
</style>
</head>
<body>

<header class="site-header">
  <div class="brand"><span class="brand-dot"></span><span>Highcrest<br>Financial</span></div>
  <nav class="main-nav">
    <a class="active">HOME</a><a>ABOUT US</a><a>BENEFITS</a><a>PLAN</a><a>FAQ</a><a>CONTACT US</a>
  </nav>
  <div class="call">
    <span class="call-icon"><svg width="14" height="14" viewBox="0 0 24 24"><path fill="#fff" d="M6.6 10.8c1.4 2.8 3.8 5.1 6.6 6.6l2.2-2.2c.3-.3.7-.4 1-.2 1.1.4 2.3.6 3.6.6.6 0 1 .4 1 1V20c0 .6-.4 1-1 1C10.6 21 3 13.4 3 4c0-.6.4-1 1-1h3.5c.6 0 1 .4 1 1 0 1.3.2 2.5.6 3.6.1.3 0 .7-.2 1z"/></svg></span>
    <span><small>CALL US</small><strong>+1 800 555 0142</strong></span>
  </div>
</header>

<section class="hero">
  <div class="abs" role="img" aria-label="Smiling female doctor in a white coat holding a tablet in a clinic hallway" style="left:560px;top:0;width:640px;height:600px;background:linear-gradient(90deg,rgba(0,0,0,0),rgba(240,242,246,.35))"></div>
  <div class="hero-welcome">WELCOME TO</div>
  <h1>Highcrest<br>Financial</h1>
  <div class="btn-outline">WATCH VIDEO</div>
  <svg class="play" width="100" height="100" viewBox="0 0 100 100" aria-label="Play video">
    <circle cx="50" cy="50" r="46" fill="none" stroke="#fff" stroke-width="4" opacity=".85"/>
    <circle cx="50" cy="50" r="38" fill="#fff" opacity=".9"/>
    <path d="M42 33 L68 50 L42 67Z" fill="#4a4f57"/>
  </svg>
  <svg class="hero-wave" width="1200" height="60" viewBox="0 0 1200 60">
    <path d="M0 60 L0 48 C260 8 520 4 760 30 C940 48 1080 46 1200 22 L1200 60Z" fill="#fff"/>
    <path d="M0 48 C260 8 520 4 760 30 C940 48 1080 46 1200 22" fill="none" stroke="var(--navy)" stroke-width="5"/>
  </svg>
</section>

<section class="about">
  <div class="about-photo" role="img" aria-label="Smiling female doctor in scrubs working at a laptop"></div>
  <h2 class="section-title"><span>What</span> is a Cash-Balance Plan</h2>
  <p>A cash balance plan is a retirement plan specifically for small business owners, doctors, lawyers, and other high-income professionals. It allows for the highest tax-deductible contribution limits in the market, and the older you get, the higher those limits go. You then get an option for guaranteed income for life or a one time, lump payout.</p>
</section>

<section class="benefits">
  <h2 class="section-title center-title" style="top:36px">Benefits<span class="rule"></span></h2>

  <article class="card card-tall" style="left:131px">
    <svg width="72" height="72" viewBox="0 0 72 72" fill="none" stroke="var(--navy)" stroke-width="2"><rect x="14" y="12" width="32" height="46" rx="3"/><rect x="19" y="17" width="22" height="9"/><path d="M20 32h5M29 32h5M38 32h2M20 39h5M29 39h5M38 39h2M20 46h5M29 46h5M38 46h2"/><path d="M46 20h10v34H46M40 58h20"/></svg>
    <h3>Highest Tax Deductible<br>Contributions Allowed</h3>
    <p>Most retirement plans in the US (IRAs, 401(k), SEP) allow $7k, $27k, or $61k a year to be contributed to retirement plans. This is a major disadvantage to individuals who have a significant income. These plans go as high as $417k.</p>
  </article>
  <article class="card card-tall" style="left:450px">
    <svg width="72" height="72" viewBox="0 0 72 72" fill="none" stroke="var(--navy)" stroke-width="2"><circle cx="20" cy="52" r="7"/><circle cx="34" cy="56" r="7"/><path d="M24 46 L50 12M30 50 L56 16"/><rect x="42" y="30" width="18" height="26" rx="2"/><path d="M46 36h10M46 43h3M52 43h3M46 49h3M52 49h3"/><circle cx="48" cy="16" r="7"/><path d="M48 12v8"/></svg>
    <h3>Significantly reduce<br>your taxes</h3>
    <p>Because these plans are tax-advantaged, the contributions are 100% tax deductible. That means an individual who contributes the full $417k annually will reduce their taxes by as much as $100k a year.</p>
  </article>
  <article class="card card-tall" style="left:769px">
    <svg width="72" height="72" viewBox="0 0 72 72" fill="none" stroke="var(--navy)" stroke-width="2"><rect x="24" y="8" width="24" height="18" rx="2"/><path d="M38 12c-4 0-5 2-5 3s1 2 3 2 3 1 3 2-1 3-5 3M36 10v14"/><path d="M8 34l8 16c2 4 6 6 10 6h6M64 34l-8 16c-2 4-6 6-10 6h-6M18 40l8 8M54 40l-8 8"/></svg>
    <h3>Potential Negative<br>“Net Cost”</h3>
    <p>Many businesses are unable to contribute to their own retirement because they also have to pay for employees. Even if they want to, the cost is often prohibitive. These plans can be designed to offer a benefit to the employee and to the business owner such that they will save more in taxes than they pay on employee retirement plans.</p>
  </article>

  <article class="card card-wide" style="left:131px">
    <svg width="68" height="68" viewBox="0 0 68 68" fill="none" stroke="var(--navy)" stroke-width="2" style="flex:none"><circle cx="34" cy="34" r="11"/><path d="M37 29c-3-1-6 0-6 2s6 2 6 5-4 3-6 2M34 25v18"/><path d="M34 18V6M30 10l4-4 4 4M34 50v12M30 58l4 4 4-4M18 34H6M10 30l-4 4 4 4M50 34h12M58 30l4 4-4 4M22 22l-8-8M46 22l8-8M22 46l-8 8M46 46l8 8"/></svg>
    <div><h3>Owner &amp; Executive Weighted Benefits</h3><p>These plans allow greater contribution for owners and executives who are older with high income.</p></div>
  </article>
  <article class="card card-wide" style="left:610px">
    <svg width="68" height="68" viewBox="0 0 68 68" fill="none" stroke="var(--navy)" stroke-width="2" style="flex:none"><ellipse cx="34" cy="34" rx="30" ry="11"/><ellipse cx="34" cy="34" rx="30" ry="11" transform="rotate(60 34 34)"/><ellipse cx="34" cy="34" rx="30" ry="11" transform="rotate(-60 34 34)"/><circle cx="34" cy="30" r="5"/><path d="M26 44c0-5 4-8 8-8s8 3 8 8"/></svg>
    <div><h3>Retain and Attract Top Talent</h3><p>These plans—on top of all the benefits provided the business owners or doctors—are great for employees. Offering them helps retain and attract top talent.</p></div>
  </article>

  <svg class="benefits-wave" width="1200" height="80" viewBox="0 0 1200 80">
    <path d="M0 80 L0 66 C200 58 360 28 600 34 C840 40 1000 10 1200 26 L1200 80Z" fill="#fff"/>
    <path d="M0 66 C200 58 360 28 600 34 C840 40 1000 10 1200 26" fill="none" stroke="var(--navy)" stroke-width="8"/>
  </svg>
</section>

<section class="contrib">
  <h2 class="section-title center-title">Allowable Tax-Deductible Contribution by Age<span class="rule"></span></h2>
  <table class="rates">
    <thead><tr>
      <th style="width:135px">Starting<br>Plan at Age:</th>
      <th style="width:131px">Max<br>Monthly<br>Retirement<br>Benefit:</th>
      <th style="width:133px">Lump Sum<br>at<br>Retirement:</th>
      <th style="width:147px">Illustrative<br>Contribution<br>Limits:</th>
      <th style="width:118px">Estimated<br>Tax<br>Savings:</th>
      <th style="width:136px">“Net Cost”<br>after Tax<br>Savings:</th>
    </tr></thead>
    <tbody>
      <tr><td>40</td><td>$20,417</td><td>$2,959,124</td><td class="key">$141,358</td><td>$56,543</td><td>$84,814</td></tr>
      <tr><td>45</td><td>$20,417</td><td>$2,959,124</td><td class="key">$178,753</td><td>$71,501</td><td>$107,252</td></tr>
      <tr><td>50</td><td>$20,417</td><td>$2,959,124</td><td class="key">$246,962</td><td>$98,784</td><td>$148,177</td></tr>
      <tr><td>55</td><td>$20,417</td><td>$2,959,124</td><td class="key">$382,181</td><td>$152,872</td><td>$229,308</td></tr>
      <tr><td>60</td><td>$10,208</td><td>$1,479,561</td><td class="key">$400,418</td><td>$160,192</td><td>$240,225</td></tr>
    </tbody>
  </table>
</section>

<section class="compare">
  <h2 class="section-title center-title">Plan Contribution Limits Comparable<span class="rule"></span></h2>
  <div class="chart-label" style="left:205px;top:315px;width:110px">Annual<br>Contributio<br>ns<br>Limits</div>

  <div class="chart-label" style="left:324px;top:327px;width:90px">$6,000<br>($7000)</div>
  <div class="bar" style="left:334px;top:379px;width:67px;height:15px;background:var(--bar-ira)"></div>
  <div class="chart-label" style="left:324px;top:408px;width:90px">IRA</div>

  <div class="chart-label" style="left:464px;top:303px;width:100px">$20,500<br>($27,000)</div>
  <div class="bar" style="left:482px;top:355px;width:65px;height:37px;background:var(--bar-401k)"></div>
  <div class="chart-label" style="left:464px;top:408px;width:100px">401(k)</div>

  <div class="chart-label" style="left:613px;top:276px;width:100px">$61,000</div>
  <div class="bar" style="left:631px;top:302px;width:64px;height:90px;background:var(--bar-ps)"></div>
  <div class="chart-label" style="left:613px;top:408px;width:100px">Profit<br>Sharin<br>g</div>

  <div class="chart-label" style="left:760px;top:126px;width:100px">$416,000</div>
  <div class="bar" style="left:777px;top:150px;width:67px;height:242px;background:var(--bar-cb)"></div>
  <div class="chart-label" style="left:760px;top:408px;width:100px">Cash<br>Balance<br>Plan</div>

  <p class="chart-note">*Your contribution limits will be based on age and salary and may not reach the max contribution amount.</p>

  <svg class="compare-wave" width="1200" height="60" viewBox="0 0 1200 60">
    <path d="M0 60 L0 20 C200 40 420 36 640 18 C860 2 1040 6 1200 22 L1200 60Z" fill="#fff"/>
    <path d="M0 20 C200 40 420 36 640 18 C860 2 1040 6 1200 22" fill="none" stroke="var(--navy)" stroke-width="6"/>
  </svg>
</section>

<section class="who">
  <h2 class="section-title">Who Should Consider Such a Plan</h2>
  <p class="intro">You should learn about your options with a Cash Balance Plan design if you are a high earning executive, partner, doctor, or successful business owner and meet the following criteria:</p>
  <ul class="criteria">
    <li>You are looking to maximize your tax deductions.</li>
    <li>Your income pushes you beyond the contribution limits of the lower retirement plans such as 401(k)s, SEPs or profit sharing plans.</li>
    <li>You are in your 40s, 50s, or 60s and don’t want the “2nd best” plan.</li>
    <li>You want an option to GUARANTEE a retirement benefit.</li>
    <li>You are looking for a way to “catch-up” on retirement savings that provides massive tax savings.</li>
  </ul>
  <div class="cta">Click here what’s my eligibility?
    <svg width="40" height="12" viewBox="0 0 40 12" fill="none" stroke="#fff" stroke-width="1.6"><path d="M0 6h38M32 1l6 5-6 5"/></svg>
  </div>
  <div class="who-photo" role="img" aria-label="Smiling senior male doctor in a white coat with a stethoscope"></div>
</section>

<section class="faq">
  <h2 class="section-title center-title">FAQ<span class="rule"></span></h2>
  <ul class="faq-list">
    <li>Lorem Ipsum is simply dummy text of the printing ?<span class="chev"><svg width="10" height="6" viewBox="0 0 10 6" fill="none" stroke="#fff" stroke-width="1.5"><path d="M1 1l4 4 4-4"/></svg></span></li>
    <li>There are many variations of passages of Lorem?<span class="chev"><svg width="10" height="6" viewBox="0 0 10 6" fill="none" stroke="#fff" stroke-width="1.5"><path d="M1 1l4 4 4-4"/></svg></span></li>
    <li>Contrary to popular belief, Lorem Ipsum?<span class="chev"><svg width="10" height="6" viewBox="0 0 10 6" fill="none" stroke="#fff" stroke-width="1.5"><path d="M1 1l4 4 4-4"/></svg></span></li>
    <li>It is a long established fact that a reader will be ?<span class="chev"><svg width="10" height="6" viewBox="0 0 10 6" fill="none" stroke="#fff" stroke-width="1.5"><path d="M1 1l4 4 4-4"/></svg></span></li>
    <li>Sed ut perspiciatis unde omnis iste natus error ?<span class="chev"><svg width="10" height="6" viewBox="0 0 10 6" fill="none" stroke="#fff" stroke-width="1.5"><path d="M1 1l4 4 4-4"/></svg></span></li>
  </ul>
</section>

<footer class="site-footer">
  <svg class="footer-wave" width="1200" height="289" viewBox="0 0 1200 289">
    <path d="M0 30 C260 44 520 46 760 34 C960 22 1100 6 1200 4 L1200 289 L0 289Z" fill="var(--footer)"/>
    <path d="M0 30 C260 44 520 46 760 34 C960 22 1100 6 1200 4" fill="none" stroke="#b9bcc3" stroke-width="8"/>
  </svg>
  <div class="brand"><span class="brand-dot"></span><span>Highcrest<br>Financial</span></div>
  <div class="follow">FOLLOW US
    <span class="social" role="img" aria-label="Social profile link"></span>
    <span class="social" role="img" aria-label="Social profile link"></span>
    <span class="social" role="img" aria-label="Social profile link"></span>
  </div>
  <nav class="footer-nav"><span>HOME</span><span>ABOUT US</span><span>BENEFITS</span><span>PLAN</span><span>FAQ</span><span>CONTACT US</span></nav>
  <p class="copyright">Copyright © 2022 All Rights Reserved</p>
</footer>

</body>
</html>
```